Awesome photographers card for an awesome new business

Double sided business card Black background and silver logo in middle on one side. Details on otherside. please keep it simple

Industry/Entity Type

Photographer

Contact Information for Business Card

Gerald Fenwick
0452817360
GeraldFenwickPhotography47@mailbox.test
www.GeraldFenwickPhotography.test.au
Instagram _Gerald_fenwick

Requirements
Must have
• My logo in Silver
• please use instagram logo instead of "Instagram"

```html
<!DOCTYPE html>
<html lang="en">
<head>
<meta charset="utf-8">
<title>Gerald Fenwick Photography – Business Card</title>
<link href="https://fonts.googleapis.com/css2?family=Roboto:wght@400;500&family=Roboto+Condensed:wght@700&display=swap" rel="stylesheet">
<style>
  :root {
    --backdrop: #ecebe8;
    --card-black: #1a1b1d;
    --card-white: #f4f4f4;
    --silver: #b9b9bb;
    --ink: #5a5a5a;
    --ink-strong: #555555;
    --web-white: #f2f2f2;
  }
  * { margin: 0; padding: 0; box-sizing: border-box; }
  html, body {
    width: 1200px; height: 960px; overflow: hidden;
    background: var(--backdrop);
    font-family: "Roboto", Arial, sans-serif;
  }
  .canvas { position: relative; width: 1200px; height: 960px; }

  .card {
    position: absolute; left: 320px; width: 600px; height: 342px;
    border-radius: 18px;
  }
  .card--front { top: 108px; background: var(--card-black); }
  .card--back  { top: 493px; background: var(--card-white); }

  .front-mark {
    position: absolute; left: 0; right: 0; top: 240px; transform: translateY(-50%);
    text-align: center; color: var(--silver);
    font-size: 42px; font-weight: 400; letter-spacing: 1px;
  }
  .front-web {
    position: absolute; left: 0; right: 0; top: 290px;
    text-align: center; color: var(--web-white);
    font-size: 14px; letter-spacing: 2.2px;
  }

  .badge {
    position: absolute; left: 37px; top: 35px; width: 150px; height: 150px;
    border: 3px solid #7d7d7d; border-radius: 50%;
    display: flex; align-items: center; justify-content: center;
  }
  .badge__name {
    color: var(--ink); font-size: 17px; font-weight: 500; text-align: center; line-height: 1.2;
  }

  .owner-name {
    position: absolute; right: 35px; top: 194px;
    font-family: "Roboto Condensed", "Arial Narrow", sans-serif;
    font-weight: 700; font-size: 22px; color: var(--ink-strong);
  }
  .contact-list {
    position: absolute; right: 35px; top: 238px; list-style: none;
  }
  .contact-list li {
    display: flex; justify-content: flex-end; align-items: center;
    height: 19.3px; font-size: 14px; color: var(--ink);
  }
  .contact-list svg { margin-left: 14px; width: 13px; height: 13px; fill: var(--ink); }
</style>
</head>
<body>
<main class="canvas">
  <section class="card card--front" aria-label="Card front">
    <div class="front-mark">Gerald Fenwick</div>
    <div class="front-web">www.GeraldFenwickPhotography.test.au</div>
  </section>

  <section class="card card--back" aria-label="Card back">
    <div class="badge"><span class="badge__name">Gerald<br>Fenwick</span></div>
    <h1 class="owner-name">GERALD FENWICK</h1>
    <ul class="contact-list">
      <li>0452817360
        <svg viewBox="0 0 16 16"><path d="M3.5 1l3 3-2 2c1 2 3 4 5 5l2-2 3 3-2 3C7 14 2 9 1 3z"/></svg>
      </li>
      <li>GeraldFenwickPhotography47@mailbox.test
        <svg viewBox="0 0 16 16"><path d="M1 3h14v10H1z M2 4l6 5 6-5" fill="none" stroke="#5a5a5a" stroke-width="1.6"/><path d="M1 3h14v2L8 10 1 5z"/></svg>
      </li>
      <li>www.GeraldFenwickPhotography.test.au
        <svg viewBox="0 0 16 16"><circle cx="8" cy="8" r="7"/><path d="M1 8h14M8 1c-3 4-3 10 0 14M8 1c3 4 3 10 0 14" fill="none" stroke="#f4f4f4" stroke-width="1.2"/></svg>
      </li>
      <li>Gerald_fenwick
        <svg viewBox="0 0 16 16"><rect x="1" y="1" width="14" height="14" rx="2"/></svg>
      </li>
    </ul>
  </section>
</main>
</body>
</html>
```